New Business Card Design Project

I need a design for business cards, i am an electrical business called "Corvane Electrical and Communications" i need the cards to be double sided with the company logo on the back (attached) the front needs to say my company name, web site, email address, telephone number, and ABN number and electrical license number. I am open to different arrangements of the information but would like the background to be incorporating something electrical or something that looks smart. open to all additional ideas also.

The company colours are orange and grey see logo attached.

Business Name: Corvane Electrical and Communications
Website: corvaneelectricalandcomms.example.com.au
Email: brent@corvaneelectricalandcomms.example.com.au
Telephone(mobile): 0481209736
ABN: 71208349162
Lic No: 418273D

Target Market(s)

Business entities, Project Managers, Accounts, Clients

Industry/Entity Type

Electrician

Contact Information for Business Card

I need a design for business cards, i am an electrical business called "Corvane Electrical and Communications" i need the cards to be double sided with the company logo on the back (attached) the front needs to say my company name

Font styles to use
Serif
Sans Serif

Colors
f37122
5c5c5c

Requirements
Must have
• Must have the Logo on the back open to different ways of it being on the back but had in mind to keep it central but again open to other options
Nice to have
• A real modern cool background that is eye catching yet contemporary
Should not have
• No backgrounds of a light bulb or plug or anything like that

```html
<!DOCTYPE html>
<html lang="en">
<head>
<meta charset="utf-8">
<title>Corvane Electrical and Communications – Business Card</title>
<link rel="stylesheet" href="https://fonts.googleapis.com/css2?family=Saira:wght@400;500;600&display=swap">
<style>
  :root {
    --backdrop: #8e8f8f;
    --card-light: #ececee;
    --card-dark: #48484b;
    --brand-orange: #e39a1c;
    --ink-grey: #4f4f52;
    --logo-light: #ececee;
  }
  * { box-sizing: border-box; margin: 0; padding: 0; }
  html, body {
    width: 1105px;
    height: 1200px;
    overflow: hidden;
  }
  body {
    background: var(--backdrop);
    position: relative;
    font-family: "Saira", Arial, sans-serif;
  }
  .card {
    position: absolute;
    left: 182px;
    width: 746px;
    height: 427px;
    background: var(--card-light);
    overflow: hidden;
  }
  .card--front { top: 119px; }
  .card--back { top: 637px; }

  .card-band {
    position: absolute;
    inset: 0;
    width: 746px;
    height: 427px;
  }

  .wordmark {
    position: absolute;
    font-weight: 600;
    letter-spacing: 0.04em;
    line-height: 1;
    display: flex;
    align-items: center;
    gap: 14px;
  }
  .wordmark__dot {
    width: 22px;
    height: 22px;
    border-radius: 50%;
    background: currentColor;
    flex: none;
  }
  .wordmark__text { display: flex; flex-direction: column; gap: 10px; }
  .wordmark__name { font-size: 62px; }
  .wordmark__sub { font-size: 17px; letter-spacing: 0.06em; }

  .card--front .wordmark {
    left: 26px;
    top: 70px;
    color: var(--logo-light);
  }
  .card--back .wordmark {
    left: 0;
    right: 0;
    top: 150px;
    justify-content: center;
    color: var(--ink-grey);
  }
  .card--back .wordmark__text { align-items: flex-start; }

  .contact-list {
    position: absolute;
    left: 24px;
    top: 322px;
    list-style: none;
    color: var(--ink-grey);
    font-size: 16px;
  }
  .contact-list li {
    display: flex;
    align-items: center;
    gap: 10px;
    height: 30px;
  }
  .contact-list svg { width: 18px; height: 18px; flex: none; }
  .contact-list .phone-number { font-size: 19px; }

  .holder {
    position: absolute;
    right: 22px;
    top: 290px;
    text-align: right;
    color: var(--ink-grey);
    font-size: 19px;
    line-height: 30px;
  }
  .holder__name {
    color: var(--brand-orange);
    font-size: 27px;
    line-height: 32px;
    letter-spacing: 0.01em;
  }
</style>
</head>
<body>

  <section class="card card--front" aria-label="Card front">
    <svg class="card-band" viewBox="0 0 746 427" aria-hidden="true">
      <polygon points="0,0 746,0 746,265 435,265 412,278 0,278" fill="var(--card-dark)"/>
      <polygon points="0,278 412,278 435,265 444,265 418,292 0,292" fill="var(--brand-orange)"/>
    </svg>

    <div class="wordmark">
      <span class="wordmark__dot"></span>
      <span class="wordmark__text">
        <span class="wordmark__name">CORVANE</span>
        <span class="wordmark__sub">ELECTRICAL &amp; COMMUNICATIONS</span>
      </span>
    </div>

    <ul class="contact-list">
      <li>
        <svg viewBox="0 0 18 18" aria-hidden="true">
          <rect x="4.5" y="1" width="9" height="16" rx="1.8" fill="var(--brand-orange)"/>
          <rect x="6" y="3" width="6" height="10" fill="var(--card-light)"/>
          <circle cx="9" cy="14.8" r="0.9" fill="var(--card-light)"/>
        </svg>
        <span class="phone-number">0481209736</span>
      </li>
      <li>
        <svg viewBox="0 0 18 18" aria-hidden="true">
          <rect x="1.5" y="4" width="15" height="10" fill="var(--brand-orange)"/>
          <polyline points="1.5,4 9,10 16.5,4" fill="none" stroke="var(--card-light)" stroke-width="1.2"/>
        </svg>
        <span>brent@corvaneelectricalandcomms.example.com.au</span>
      </li>
      <li>
        <svg viewBox="0 0 18 18" aria-hidden="true">
          <circle cx="9" cy="9" r="7.5" fill="var(--brand-orange)"/>
          <ellipse cx="9" cy="9" rx="3.2" ry="7.5" fill="none" stroke="var(--card-light)" stroke-width="1"/>
          <line x1="1.5" y1="9" x2="16.5" y2="9" stroke="var(--card-light)" stroke-width="1"/>
        </svg>
        <span>corvaneelectricalandcomms.example.com.au</span>
      </li>
    </ul>

    <div class="holder">
      <p class="holder__name">DARA WHITLOCK</p>
      <p class="holder__role">CEO/FOUNDER</p>
      <p class="holder__abn">ABN: 71208349162</p>
      <p class="holder__licence">Lic No: 418273D</p>
    </div>
  </section>

  <section class="card card--back" aria-label="Card back">
    <div class="wordmark">
      <span class="wordmark__dot"></span>
      <span class="wordmark__text">
        <span class="wordmark__name">CORVANE</span>
        <span class="wordmark__sub">ELECTRICAL &amp; COMMUNICATIONS</span>
      </span>
    </div>
  </section>

</body>
</html>
```